Construction company that specializes in roofing and siding

https://maplecrestbuild.example/featured-projects/

https://www.bramwickhomesllc.example/#

https://www.tallgrovecontractors.example/residential-siding-services/

Please model a website after these examples
I posted a doc that has some content to get you started. I will upload more content and photos as the site progresses.

Coded - Design and coding required

5+ page

```html
<!DOCTYPE html>
<html lang="en">
<head>
<meta charset="utf-8">
<title>Stonebridge Construction — Roofing &amp; Siding</title>
<link href="https://fonts.googleapis.com/css2?family=Krona+One&family=Poppins:wght@400;500;600;700&display=swap" rel="stylesheet">
<style>
:root{
  --orange:#ff7a00;
  --ink:#111111;
  --dark:#1c1c1c;
  --text:#333333;
  --muted:#555555;
  --light:#f2f2f2;
  --white:#ffffff;
  --line:#cfcfcf;
}
*{box-sizing:border-box;margin:0;padding:0}
html,body{width:1200px;height:4422px;overflow:hidden}
body{position:relative;background:var(--white);font-family:"Poppins",sans-serif;color:var(--text)}
.abs{position:absolute}
.display{font-family:"Krona One",sans-serif;text-transform:uppercase;color:var(--ink);letter-spacing:1px}
.btn{position:absolute;display:flex;align-items:center;justify-content:center;border-radius:30px;background:var(--orange);color:var(--white);font-family:"Krona One",sans-serif;font-size:14px;text-transform:uppercase;letter-spacing:1px}
.photo{position:absolute}

/* header */
.brand{position:absolute;display:flex;align-items:center;gap:12px}
.brand-mark{width:48px;height:48px;background:#444}
.brand-name{font-family:"Poppins",sans-serif;font-weight:700;font-size:20px;color:#444;letter-spacing:1px;text-transform:uppercase}
.phone{left:660px;top:10px;display:flex;align-items:center;gap:12px;font-family:"Krona One",sans-serif;font-size:16px;color:var(--ink)}
.phone-icon{width:40px;height:40px;border-radius:50%;background:#444;display:flex;align-items:center;justify-content:center}
.quote-btn{left:912px;top:10px;width:213px;height:42px;background:var(--ink);font-size:12px}
.nav{position:absolute;left:460px;top:62px;width:740px;height:46px;background:var(--orange);display:flex;align-items:center;z-index:2}
.nav a{color:var(--white);text-decoration:none;font-size:12px;font-weight:600;text-transform:uppercase;padding:0 18px;height:46px;display:flex;align-items:center}
.nav a.active{background:var(--ink);padding:0 24px}

/* hero */
.hero{left:0;top:82px;width:1200px;height:570px;background:linear-gradient(100deg,#7a3a12 0%,#a0521e 30%,#5e5c58 65%,#8f8b85 100%)}
.hero-title{left:75px;top:245px;font-size:50px;line-height:50px;color:var(--white)}
.hero-sub{left:75px;top:350px;width:540px;font-size:22px;line-height:30px;color:var(--white);font-weight:500}
.dots{left:75px;top:592px;display:flex;gap:8px}
.dots span{width:12px;height:12px;border-radius:50%;background:var(--ink)}
.dots span:first-child{background:var(--white)}
.form{left:765px;top:145px;width:360px;height:472px;background:#161616;border-radius:10px;padding:22px 22px}
.form h3{font-size:20px;color:var(--white);margin-bottom:16px}
.field{height:44px;border-radius:22px;background:var(--white);margin-bottom:14px;font-size:12px;color:var(--ink);padding:0 18px;display:flex;align-items:center;justify-content:space-between}
.field.msg{height:92px;border-radius:18px;align-items:flex-start;padding-top:14px}
.form .submit{position:static;height:44px;font-size:15px}

/* about */
.about-img{left:75px;top:730px;width:390px;height:415px;background:linear-gradient(160deg,#d9d4cc,#8a8780 60%,#4d4b48)}
.h2{font-size:38px;line-height:48px}
.about-h{left:523px;top:765px}
.body-p{font-size:14px;line-height:28px;color:var(--text)}
.about-p{left:523px;top:875px;width:590px}
.divider{left:75px;top:1232px;width:1050px;height:16px;background:#d4d4d4}

/* services */
.center-h{left:0;width:1200px;text-align:center}
.card-img{position:absolute;width:328px;height:226px;border-radius:10px}
.card-label{position:absolute;width:288px;height:70px;background:var(--white);border-radius:8px;box-shadow:0 6px 14px rgba(0,0,0,.18);display:flex;align-items:center;justify-content:space-between;padding:0 24px 0 18px;font-family:"Krona One",sans-serif;font-size:14px;text-transform:uppercase;color:var(--ink);line-height:20px}

/* cta band */
.band{left:0;top:2055px;width:1200px;height:121px;background:linear-gradient(90deg,#111 0%,#3a3530 60%,#5a4f44 100%)}

/* promise */
.owner-img{left:108px;top:2345px;width:354px;height:380px;border-radius:40px;background:linear-gradient(170deg,#c9a57a,#7a5c44 55%,#4a3a2e)}

/* work */
.work{left:0;top:2805px;width:1200px;height:525px;background:var(--light)}
.circle-arrow{position:absolute;width:34px;height:34px;border-radius:50%;background:var(--ink);display:flex;align-items:center;justify-content:center}

/* reviews */
.review{position:absolute;top:3473px;width:328px;height:214px;border:2px solid #d6d6d6;border-radius:8px;background:#f5f5f5;padding:22px 18px}
.review .qt{width:40px;height:40px;border-radius:50%;background:#ddd;display:flex;align-items:center;justify-content:center;font-family:"Krona One",sans-serif;font-size:22px;color:var(--ink);float:left;margin-right:16px}
.review h4{font-size:16px;font-weight:600;color:var(--ink);padding-top:4px}
.stars{color:var(--orange);font-size:15px;letter-spacing:3px}
.review p{clear:both;font-size:13px;line-height:24px;color:var(--text);padding-top:22px}

/* bottom cta */
.cta{left:0;top:3765px;width:1200px;height:323px;background:linear-gradient(180deg,#1a1d22,#2b3138 60%,#1e2226)}

/* footer */
.foot-col{position:absolute;top:4146px;font-size:13px;line-height:29px;color:var(--ink)}
.foot-col h5{font-size:15px;font-weight:700;margin-bottom:6px}
.social{left:75px;top:4320px;display:flex;gap:16px}
.social span{width:18px;height:18px;border-radius:50%;background:var(--ink)}
</style>
</head>
<body>

<!-- Header -->
<div class="brand" style="left:75px;top:15px">
  <div class="brand-mark"></div>
  <div class="brand-name">Stonebridge</div>
</div>
<div class="abs phone">
  <div class="phone-icon"><svg width="18" height="18" viewBox="0 0 24 24"><path fill="#fff" d="M6.6 10.8a15 15 0 0 0 6.6 6.6l2.2-2.2a1 1 0 0 1 1-.25 11.4 11.4 0 0 0 3.6.57 1 1 0 0 1 1 1V20a1 1 0 0 1-1 1A17 17 0 0 1 3 4a1 1 0 0 1 1-1h3.5a1 1 0 0 1 1 1c0 1.25.2 2.45.57 3.57a1 1 0 0 1-.25 1z"/></svg></div>
  +1 555-014-2290
</div>
<div class="btn quote-btn">Request a Quote</div>
<nav class="nav">
  <a class="active">Home</a><a>About Us</a><a>Services</a><a>Our Work</a><a>Blog</a><a>Reviews</a><a>Contact Us</a>
</nav>

<!-- Hero -->
<div class="photo hero" role="img" aria-label="Roofer in a cap and orange safety vest installing metal roofing"></div>
<h1 class="abs display hero-title">Stone<br>Construction</h1>
<p class="abs hero-sub">We are a Construction company specializes in roofing and siding.</p>
<div class="btn" style="left:77px;top:425px;width:198px;height:54px">Read More</div>
<div class="abs dots"><span></span><span></span><span></span><span></span></div>

<div class="abs form">
  <h3 class="display" style="color:#fff">Get a Free Quote</h3>
  <div class="field">Enter Name</div>
  <div class="field">Email Address</div>
  <div class="field">Phone No</div>
  <div class="field">Select Services <span>&#8693;</span></div>
  <div class="field msg">Message</div>
  <div class="btn submit">Submit</div>
</div>

<!-- About -->
<div class="photo about-img" role="img" aria-label="Roofer in hard hat collage framed in a shield shape"></div>
<h2 class="abs display h2 about-h">About Stonebridge<br>Construction</h2>
<p class="abs body-p about-p">In 2016 Dale Harper started helping people with their home improvement projects. His very first job was installing window trim for a wonderful homeowner in Cedar Hollow MN. He did his best work and made sure he treated his first customer like family. Afterall, his first customer was Marla Harper, his Mom.</p>
<div class="btn" style="left:523px;top:1040px;width:198px;height:54px">Read More</div>
<div class="abs divider"></div>

<!-- Services -->
<h2 class="abs display h2 center-h" style="top:1310px">What We Do</h2>

<div class="card-img" style="left:75px;top:1403px;background:linear-gradient(160deg,#8fae6a,#5f6670 55%,#c9c29e)" role="img" aria-label="Shingled roof on a house"></div>
<div class="card-label" style="left:85px;top:1593px">Roofing <svg width="20" height="20" viewBox="0 0 24 24"><path fill="none" stroke="#ff7a00" stroke-width="3" d="M3 12h17M13 5l7 7-7 7"/></svg></div>
<div class="card-img" style="left:434px;top:1403px;background:linear-gradient(160deg,#e8ebe8,#8a8a5c 55%,#8a4a30)" role="img" aria-label="House with green siding"></div>
<div class="card-label" style="left:444px;top:1593px">Siding <svg width="20" height="20" viewBox="0 0 24 24"><path fill="none" stroke="#ff7a00" stroke-width="3" d="M3 12h17M13 5l7 7-7 7"/></svg></div>
<div class="card-img" style="left:794px;top:1403px;background:linear-gradient(160deg,#6f9ed4,#3b4a5a 55%,#c9ccd0)" role="img" aria-label="Roof edge with gutter and downspout"></div>
<div class="card-label" style="left:804px;top:1593px">Gutters <svg width="20" height="20" viewBox="0 0 24 24"><path fill="none" stroke="#ff7a00" stroke-width="3" d="M3 12h17M13 5l7 7-7 7"/></svg></div>

<div class="card-img" style="left:75px;top:1709px;background:linear-gradient(160deg,#cfd6d8,#f1f2f0 50%,#9aa3a6)" role="img" aria-label="Gloved hands installing a window"></div>
<div class="card-label" style="left:85px;top:1900px">Windows <svg width="20" height="20" viewBox="0 0 24 24"><path fill="none" stroke="#ff7a00" stroke-width="3" d="M3 12h17M13 5l7 7-7 7"/></svg></div>
<div class="card-img" style="left:434px;top:1709px;background:linear-gradient(160deg,#a8c9e0,#4f7fb0 45%,#3a3d44)" role="img" aria-label="Roofer using a nail gun on shingles"></div>
<div class="card-label" style="left:444px;top:1900px">Repair <svg width="20" height="20" viewBox="0 0 24 24"><path fill="none" stroke="#ff7a00" stroke-width="3" d="M3 12h17M13 5l7 7-7 7"/></svg></div>
<div class="card-img" style="left:794px;top:1709px;background:linear-gradient(160deg,#5e6e58,#8a7a5a 50%,#c86a2a)" role="img" aria-label="Crew clearing fallen trees after a storm"></div>
<div class="card-label" style="left:804px;top:1900px">Storm Damage<br>Repair <svg width="20" height="20" viewBox="0 0 24 24"><path fill="none" stroke="#ff7a00" stroke-width="3" d="M3 12h17M13 5l7 7-7 7"/></svg></div>

<!-- CTA band -->
<div class="photo band" role="img" aria-label="Dark roofing background"></div>
<h2 class="abs display" style="left:75px;top:2095px;font-size:36px;color:#fff">Get Started Today</h2>
<div class="btn" style="left:828px;top:2088px;width:297px;height:54px">Get Started Now</div>

<!-- Promise -->
<div class="photo owner-img" role="img" aria-label="Owner in a hard hat and plaid shirt"></div>
<h2 class="abs display h2" style="left:523px;top:2388px">The Stonebridge<br>Promise</h2>
<p class="abs body-p" style="left:523px;top:2498px;width:600px">You deserve timely service, high quality materials, expert installation, and an rock-solid warranty. That is what we promise to deliver. I invite you to put us to the test today.</p>
<p class="abs body-p" style="left:523px;top:2598px">Sincerely,</p>
<p class="abs display" style="left:523px;top:2626px;font-size:15px">Dale Harper, Owner</p>
<p class="abs body-p" style="left:523px;top:2648px">Stonebridge Construction</p>

<!-- Work -->
<div class="abs work"></div>
<h2 class="abs display h2 center-h" style="top:2872px">See Our Work</h2>
<div class="photo" style="left:0;top:2935px;width:293px;height:330px;background:linear-gradient(160deg,#c9b79c,#9a8a74);opacity:.55" role="img" aria-label="Roofer at work on shingles"></div>
<div class="photo" style="left:317px;top:2935px;width:285px;height:330px;background:linear-gradient(180deg,#b4c3c6,#c8b48c 45%,#6a5a48)" role="img" aria-label="Roof frame before the project"></div>
<div class="photo" style="left:602px;top:2935px;width:284px;height:330px;background:linear-gradient(180deg,#7a9a58,#3e4654 45%,#5e6a50)" role="img" aria-label="Finished shingle roof after the project"></div>
<div class="abs" style="left:601px;top:2935px;width:2px;height:330px;background:#fff"></div>
<div class="abs" style="left:587px;top:3085px;width:30px;height:30px;border-radius:50%;background:#fff;display:flex;align-items:center;justify-content:center;font-size:12px;color:#333">&#8249;&#8250;</div>
<div class="abs" style="left:332px;top:3240px;font-size:13px;font-weight:600;color:#fff">BEFORE</div>
<div class="abs" style="left:824px;top:3240px;font-size:13px;font-weight:600;color:#fff">AFTER</div>
<div class="photo" style="left:910px;top:2935px;width:290px;height:330px;background:linear-gradient(160deg,#d0a89a,#d8d6d2 55%,#9a9894);opacity:.6" role="img" aria-label="Worker installing a gutter"></div>
<div class="circle-arrow" style="left:77px;top:3084px"><svg width="16" height="16" viewBox="0 0 24 24"><path fill="none" stroke="#fff" stroke-width="3" d="M21 12H4M11 5l-7 7 7 7"/></svg></div>
<div class="circle-arrow" style="left:1092px;top:3084px"><svg width="16" height="16" viewBox="0 0 24 24"><path fill="none" stroke="#fff" stroke-width="3" d="M3 12h17M13 5l7 7-7 7"/></svg></div>

<!-- Reviews -->
<h2 class="abs display h2" style="left:75px;top:3385px">Customer Reviews</h2>
<div class="circle-arrow" style="left:1040px;top:3392px"><svg width="16" height="16" viewBox="0 0 24 24"><path fill="none" stroke="#fff" stroke-width="3" d="M21 12H4M11 5l-7 7 7 7"/></svg></div>
<div class="circle-arrow" style="left:1092px;top:3392px;background:var(--orange)"><svg width="16" height="16" viewBox="0 0 24 24"><path fill="none" stroke="#fff" stroke-width="3" d="M3 12h17M13 5l7 7-7 7"/></svg></div>

<div class="review" style="left:75px"><div class="qt">&#8220;</div><h4>Name Heading</h4><div class="stars">&#9733;&#9733;&#9733;&#9733;&#9733;</div><p>Sed ut perspiciatis unde omnis iste natus error sit voluptatem accusantium doloremque laudantium, totam rem aperiam, eaque ipsa.</p></div>
<div class="review" style="left:436px"><div class="qt">&#8220;</div><h4>Name Heading</h4><div class="stars">&#9733;&#9733;&#9733;&#9733;&#9733;</div><p>Sed ut perspiciatis unde omnis iste natus error sit voluptatem accusantium doloremque laudantium, totam rem aperiam, eaque ipsa.</p></div>
<div class="review" style="left:797px"><div class="qt">&#8220;</div><h4>Name Heading</h4><div class="stars">&#9733;&#9733;&#9733;&#9733;&#9733;</div><p>Sed ut perspiciatis unde omnis iste natus error sit voluptatem accusantium doloremque laudantium, totam rem aperiam, eaque ipsa.</p></div>

<!-- Bottom CTA -->
<div class="photo cta" role="img" aria-label="Worker on a roof in dark tones"></div>
<h2 class="abs display center-h" style="top:3832px;font-size:38px;color:#fff">Get Started Today</h2>
<p class="abs center-h" style="top:3890px;font-size:15px;line-height:27px;color:#fff;padding:0 190px">Duis aute irure dolor in reprehenderit in voluptate velit esse cillum dolore eu fugiat nulla sint occaecat cupi atat non proident, sunt in culpa qui officia deserunt mollit anim id est laborum.</p>
<div class="btn" style="left:451px;top:3960px;width:298px;height:56px">Get Started Now</div>

<!-- Footer -->
<div class="brand" style="left:75px;top:4125px">
  <div class="brand-mark"></div>
  <div class="brand-name">Stonebridge</div>
</div>
<p class="abs" style="left:75px;top:4245px;font-size:13px;line-height:24px;color:var(--ink)">Copyright © 2024 Stonebridge Construction<br>All rights reserved.</p>
<div class="abs social" aria-label="Social links"><span></span><span></span><span></span><span></span><span></span></div>

<div class="foot-col" style="left:433px"><h5>SITE MAP</h5>Home<br>About Us<br>Services<br>Our Work<br>Blog<br>Reviews<br>Contact Us</div>
<div class="foot-col" style="left:652px"><h5>SERVICES</h5>Roofing<br>Siding<br>Gutters<br>Windows<br>Repair<br>Storm damage repair</div>
<div class="foot-col" style="left:888px;line-height:24px"><h5 style="margin-bottom:10px">CONTACT US</h5>48 Quarry Lane, Suite 12,<br>Millbrook 55021, United States<br><span style="display:block;margin-top:12px">+1 555-014-2290</span><span style="display:block;margin-top:12px">hello@stonebridgebuild.example</span></div>

</body>
</html>
```